BOLD & MINIMALIST DESIGN NEEDED

We want a very bold but minimalistic business card design that is impactful and utilizes both sides of the business card. Our current logo is included for your use.

We want bold fonts and good use of negative space. We don't want the logo to overpower the design.

Target Market(s)

Professionals who are building new commercial buildings.

Industry/Entity Type

Construction

Contact Information for Business Card

Name, Title, email, office phone, cell phone, website

Font styles to use
Serif
Sans Serif

Requirements
Must have
• Bold design!

```html
<!DOCTYPE html>
<html lang="en">
<head>
<meta charset="utf-8">
<title>Ridgemont Design + Build — Business Card</title>
<link rel="stylesheet" href="https://fonts.googleapis.com/css2?family=Montserrat:wght@400;500;800;900&display=swap">
<style>
  :root {
    --bg: #222222;
    --card: #141414;
    --green: #7cc242;
    --white: #ffffff;
    --silver: #cfcfcf;
    --muted: #e6e6e6;
  }
  * { box-sizing: border-box; margin: 0; padding: 0; }
  html, body { width: 1200px; height: 711px; overflow: hidden; background: var(--bg); }
  body { font-family: "Montserrat", Arial, sans-serif; color: var(--white); }
  .stage { position: relative; width: 1200px; height: 711px; }
  .card {
    position: absolute; top: 93px; width: 300px; height: 525px;
    background: var(--card); border-radius: 22px;
    box-shadow: 0 14px 30px rgba(0,0,0,.55);
  }
  .card--back { left: 250px; }
  .card--front { left: 650px; }

  /* back side */
  .back-mark {
    position: absolute; left: 0; right: 0; top: 50%; transform: translateY(-50%);
    text-align: center;
  }
  .back-mark__name {
    font-weight: 900; font-size: 40px; letter-spacing: 1px; color: var(--silver); line-height: 1;
  }
  .back-mark__tag {
    margin-top: 10px; font-weight: 400; font-size: 13px; letter-spacing: 7px; color: var(--silver);
  }

  /* front side */
  .brand { position: absolute; top: 70px; left: 0; right: 0; text-align: center; }
  .brand__square { display: inline-block; width: 34px; height: 34px; background: var(--green); margin-bottom: 12px; }
  .brand__name { font-weight: 900; font-size: 34px; line-height: 1; color: var(--white); letter-spacing: .5px; }
  .brand__tag { margin-top: 8px; font-weight: 400; font-size: 11px; letter-spacing: 6px; color: var(--white); }

  .person { position: absolute; top: 196px; left: 0; right: 0; text-align: center; }
  .person__name { font-weight: 800; font-size: 25px; color: var(--green); letter-spacing: .5px; }
  .person__title { font-weight: 400; font-size: 12px; letter-spacing: 1px; color: var(--white); margin-top: 2px; }

  .dots { position: absolute; left: 0; width: 300px; height: 30px; }
  .dots--contact { top: 256px; }
  .dots--address { top: 395px; }

  .contact-list {
    position: absolute; top: 294px; left: 0; right: 0; list-style: none;
    text-align: center; font-size: 13px; line-height: 20px; color: var(--muted);
  }
  .address {
    position: absolute; top: 436px; left: 0; right: 0; text-align: center;
    font-style: normal; font-size: 13px; line-height: 20px; color: var(--muted);
  }
</style>
</head>
<body>
<main class="stage">

  <section class="card card--back" aria-label="Card back">
    <div class="back-mark">
      <div class="back-mark__name">RIDGEMONT</div>
      <div class="back-mark__tag">DESIGN + BUILD</div>
    </div>
  </section>

  <section class="card card--front" aria-label="Card front">
    <div class="brand">
      <span class="brand__square" aria-hidden="true"></span>
      <div class="brand__name">RIDGEMONT</div>
      <div class="brand__tag">DESIGN + BUILD</div>
    </div>

    <div class="person">
      <div class="person__name">ARJUN MEHTA</div>
      <div class="person__title">OWNER-CEO</div>
    </div>

    <svg class="dots dots--contact" viewBox="0 0 300 30" aria-hidden="true">
      <g fill="var(--green)">
        <circle cx="14" cy="15" r="2.5"/><circle cx="26" cy="15" r="3.5"/><circle cx="40" cy="15" r="4.5"/><circle cx="55" cy="15" r="5.5"/>
        <circle cx="246" cy="15" r="5.5"/><circle cx="261" cy="15" r="4.5"/><circle cx="275" cy="15" r="3.5"/><circle cx="287" cy="15" r="2.5"/>
        <circle cx="96" cy="15" r="12"/><circle cx="128" cy="15" r="12"/><circle cx="160" cy="15" r="12"/><circle cx="192" cy="15" r="12"/>
      </g>
      <g fill="none" stroke="var(--card)" stroke-width="1.6" stroke-linecap="round" stroke-linejoin="round">
        <!-- phone handset -->
        <path d="M90 10 q6 -3 12 0 l-1 3 h-2 l-1 -2 h-4 l-1 2 h-2 z M91 14 h10 v5 h-10 z"/>
        <!-- mobile -->
        <rect x="124" y="8" width="8" height="14" rx="1.5"/>
        <!-- mail -->
        <rect x="153" y="10" width="14" height="10" rx="1"/><path d="M153 10 l7 6 l7 -6"/>
        <!-- globe -->
        <circle cx="192" cy="15" r="7"/><path d="M185 15 h14 M192 8 q-4 7 0 14 q4 -7 0 -14"/>
      </g>
    </svg>

    <ul class="contact-list">
      <li class="contact-list__office">123 456 789</li>
      <li class="contact-list__mobile">123 456 789</li>
      <li class="contact-list__email">info@yourmail.com</li>
      <li class="contact-list__web">www.yourwebsite.com</li>
    </ul>

    <svg class="dots dots--address" viewBox="0 0 300 30" aria-hidden="true">
      <g fill="var(--green)">
        <circle cx="14" cy="15" r="2.5"/><circle cx="28" cy="15" r="3.5"/><circle cx="44" cy="15" r="4.5"/><circle cx="62" cy="15" r="5.5"/><circle cx="82" cy="15" r="6.5"/><circle cx="104" cy="15" r="7.5"/>
        <circle cx="196" cy="15" r="7.5"/><circle cx="218" cy="15" r="6.5"/><circle cx="238" cy="15" r="5.5"/><circle cx="256" cy="15" r="4.5"/><circle cx="272" cy="15" r="3.5"/><circle cx="286" cy="15" r="2.5"/>
        <circle cx="150" cy="15" r="13"/>
      </g>
      <path d="M150 23 q-6 -6 -6 -10 a6 6 0 0 1 12 0 q0 4 -6 10 z" fill="var(--white)"/>
      <circle cx="150" cy="13" r="2.2" fill="var(--green)"/>
    </svg>

    <address class="address">Your address,<br>City State, Zip 1234</address>
  </section>

</main>
</body>
</html>
```